New Business Card Design Project LORVANTI-Italy

we are LORVANTI-Italy
our company in the market for 3 years we are luxury cosmetic company and its about time for a facelift :)
i will like to have elegant luxurious and unique business card
that will give the person that get it a unique, luxurious and elegant impression
I'm VERY OPEN FOR NEW IDEAS , even duo i add a few files of things that i see on line and i like them

i add my logo as well
my website is LORVANTI.COM
(if you would like to see the main style that we have)

Target Market(s)

adult that have money :)

Industry/Entity Type

Business

Contact Information for Business Card

Name - Dario Lorvanti
Position - CEO and CO Founder
address - 4817 E Halvern
telephone - 555-384-1926
email - dario@lorvanti.com
fax - 555-384-1926
website - LORVANTI.COM

Colors
000000
959595
fbee3e
ffffff

Requirements
Must have
• big logo in GOLD color
• elegant look
• impressive
Nice to have
• not must but maybe classy pattern background
• not must but maybe emblem
• maybe clear plastic business card
Should not have
• colors
• images

```html
<!DOCTYPE html>
<html lang="en">
<head>
<meta charset="utf-8">
<title>LORVANTI Italy – Business Card</title>
<link rel="stylesheet" href="https://fonts.googleapis.com/css2?family=Cinzel:wght@500&family=Rajdhani:wght@500;600&display=swap">
<style>
  :root {
    --backdrop: #151515;
    --card: #2b2a2b;
    --gold: #d9a82b;
    --white: #f2f2f2;
    --grey: #959595;
  }
  * { margin: 0; padding: 0; box-sizing: border-box; }
  html, body { width: 1200px; height: 800px; overflow: hidden; background: var(--backdrop); }
  .canvas {
    position: relative; width: 1200px; height: 800px;
    display: flex; align-items: center; justify-content: center; gap: 60px;
  }
  .card {
    position: relative; width: 520px; height: 297px;
    background: var(--card);
    box-shadow: 0 14px 30px rgba(0,0,0,.55);
  }
  /* Front */
  .card-front {
    display: flex; flex-direction: column; align-items: center; justify-content: center; gap: 18px;
  }
  .brand-mark {
    width: 64px; height: 64px; border: 3px solid var(--gold); border-radius: 50%;
  }
  .brand-name {
    font-family: "Cinzel", serif; font-weight: 500; color: var(--gold);
    font-size: 46px; letter-spacing: 2px; line-height: 1;
  }
  .brand-origin {
    font-family: "Cinzel", serif; font-weight: 500; color: var(--gold);
    font-size: 15px; letter-spacing: 3px; margin-top: -8px;
  }
  /* Back */
  .card-back { padding: 34px 0 0 34px; }
  .holder-name {
    font-family: "Rajdhani", sans-serif; font-weight: 600; color: var(--gold);
    font-size: 20px; letter-spacing: 1px; text-transform: uppercase; line-height: 1;
  }
  .holder-role {
    font-family: "Rajdhani", sans-serif; font-weight: 500; color: var(--white);
    font-size: 14px; margin: 4px 0 14px;
  }
  .contact-list { list-style: none; }
  .contact-list li {
    display: flex; align-items: center; gap: 8px;
    font-family: "Rajdhani", sans-serif; font-weight: 500; color: var(--white);
    font-size: 14px; line-height: 21px;
  }
  .contact-list svg { width: 12px; height: 12px; fill: var(--gold); flex: none; }
  .website {
    font-family: "Rajdhani", sans-serif; font-weight: 600; color: var(--gold);
    font-size: 16px; letter-spacing: 1px; margin-top: 12px;
  }
  .emblem-area {
    position: absolute; right: 34px; top: 50%; transform: translateY(-50%);
    width: 200px; height: 200px; border: 4px solid var(--gold); border-radius: 50%;
    display: flex; align-items: center; justify-content: center;
  }
  .emblem-name {
    font-family: "Cinzel", serif; font-weight: 500; color: var(--gold);
    font-size: 24px; letter-spacing: 1px;
  }
</style>
</head>
<body>
<main class="canvas">
  <section class="card card-front" aria-label="Business card front">
    <span class="brand-mark" aria-hidden="true"></span>
    <h1 class="brand-name">LORVANTI</h1>
    <p class="brand-origin">ITALY</p>
  </section>

  <section class="card card-back" aria-label="Business card back">
    <h2 class="holder-name">Dario Lorvanti</h2>
    <p class="holder-role">CEO &amp; CO Founder</p>
    <ul class="contact-list">
      <li><svg viewBox="0 0 12 12" aria-hidden="true"><path d="M2.4 0.6l2 2-1 1.4c.7 1.5 1.8 2.6 3.3 3.3l1.4-1 2 2-1.2 1.8C5.4 10 1.9 6.5 .6 1.9z"/></svg>555-384-1926</li>
      <li><svg viewBox="0 0 12 12" aria-hidden="true"><path d="M3 0h6v3H3zM1 4h10v6H9v2H3v-2H1zM4 8v3h4V8z"/></svg>555-384-1926</li>
      <li><svg viewBox="0 0 12 12" aria-hidden="true"><path d="M0 2h12v1L6 7 0 3zM0 4.3l6 4 6-4V10H0z"/></svg>dario@lorvanti.com</li>
      <li><svg viewBox="0 0 12 12" aria-hidden="true"><path d="M6 0a4 4 0 0 1 4 4c0 3-4 8-4 8S2 7 2 4a4 4 0 0 1 4-4zm0 2.5a1.5 1.5 0 1 0 0 3 1.5 1.5 0 0 0 0-3z"/></svg>4817 E Halvern</li>
    </ul>
    <p class="website">LORVANTI.COM</p>
    <div class="emblem-area">
      <span class="emblem-name">LORVANTI</span>
    </div>
  </section>
</main>
</body>
</html>
```